4D Cradle Glimpse Luxury Ultrasound Billboard

Design a HIGH-END, MODERN billboard for my private prenatal ultrasound studio, 4D Cradle Glimpse, located in Pace, Florida.
This billboard will be viewed by drivers traveling at highway speeds, so it must be extremely clean, simple, and readable within 6 seconds.
About My Business
4D Cradle Glimpse is a private prenatal ultrasound studio specializing in:
Highest technology 4D/HD Ultrasounds
Early Gender Determination
Pregnancy Confirmation
I have been serving families for nearly 10 years and is known for creating a memorable experience, not just an ultrasound appointment.
Design Style
I DO NOT want:
Flowers
Leaves
Swirls
Glitter
Hearts everywhere
Busy backgrounds
Generic maternity stock graphics
I DO want:
Modern
Luxury
Upscale
Clean
Professional
Eye-catching
Premium medical spa feel
Colors
Use colors from my logo:
LOGO Green ( or a deep green)
Black
White
Soft Gold accents
Images:
Incorporate my professional headshot in a clean, modern way, logo, and the ultrasound images
Text
Keep wording minimal.
Primary Headline ( OPEN TO IDEAS) :
EXAMPLES ( WOULD RATHER SOMETHING MORE CATCHY)
" ADVANCED IMAGING. UNFORGETTABLE MOMENTS"
"MEET YOUR BABY BEFORE BIRTH"
Under headline:
4D Ultrasound • Early Gender • Pregnancy Confirmation
Business Name:
4D Cradle Glimpse
Private Prenatal Ultrasound Studio
Phone Number:
850-471-5923
Important
This billboard must be readable in 5–6 seconds from a moving vehicle.
Less text is better.
The phone number and business name must be visible from a distance.
The design should feel like a premium brand that immediately tells expecting parents:
“This is where I go to see my baby.”
Files Provided
Official logo
Headshot
Ultrasound images
Don’t make this look like a medical office billboard.
Make it look like a luxury baby experience billboard. That’s what separates 4D Cradle Glimpse from hospitals, OB offices, and all the new studios popping up around you. The emotional connection is what gets moms to book. ❤️
Billboard Size - 10.6” x 36”

```html
<!DOCTYPE html>
<html lang="en">
<head>
<meta charset="utf-8">
<title>4D Cradle Glimpse Billboard</title>
<link href="https://fonts.googleapis.com/css2?family=Bebas+Neue&family=Allura&display=swap" rel="stylesheet">
<style>
  :root {
    --page-bg: #eceef0;
    --deep-green: #44523f;
    --gold: #c3993a;
    --gold-light: #f3bd45;
    --slate: #3e4a4a;
    --white: #ffffff;
    --ink: #111111;
  }
  * { margin: 0; padding: 0; box-sizing: border-box; }
  html, body {
    width: 1200px;
    height: 1080px;
    overflow: hidden;
    background: var(--page-bg);
  }
  .billboard {
    position: absolute;
    left: 30px;
    top: 374px;
    width: 1140px;
    height: 331px;
    background: var(--deep-green);
    overflow: hidden;
    font-family: "Bebas Neue", "Arial Narrow", sans-serif;
    box-shadow: 0 10px 30px rgba(0,0,0,0.18);
  }
  .billboard-bands {
    position: absolute;
    inset: 0;
    width: 1140px;
    height: 331px;
  }
  .brand-plate {
    position: absolute;
    left: 47px;
    top: 24px;
    width: 298px;
    height: 153px;
    background: var(--white);
    border: 3px solid #5b6661;
    border-radius: 26px;
    box-shadow: 0 8px 10px rgba(0,0,0,0.35);
    display: flex;
    align-items: center;
    justify-content: center;
    gap: 10px;
  }
  .brand-dot {
    flex: none;
    width: 18px;
    height: 18px;
    border-radius: 50%;
    background: var(--gold);
  }
  .brand-name {
    font-size: 34px;
    line-height: 1;
    color: var(--slate);
    letter-spacing: 0.5px;
    white-space: nowrap;
  }
  .services {
    position: absolute;
    left: 47px;
    top: 204px;
    list-style: none;
  }
  .services li {
    position: relative;
    font-size: 35px;
    line-height: 38px;
    height: 38px;
    color: var(--white);
    padding-left: 15px;
    white-space: nowrap;
  }
  .services li::before {
    content: "";
    position: absolute;
    left: 0;
    top: 7px;
    width: 3px;
    height: 26px;
    background: var(--gold);
  }
  .headline {
    position: absolute;
    left: 388px;
    top: 18px;
    color: var(--white);
    font-size: 100px;
    line-height: 82px;
    font-weight: 400;
    letter-spacing: 0.5px;
    white-space: nowrap;
  }
  .headline .script-word {
    font-family: "Allura", cursive;
    color: var(--gold-light);
    font-size: 80px;
    letter-spacing: 0;
    margin-left: 10px;
    position: relative;
    top: 4px;
  }
  .contact {
    position: absolute;
    left: 397px;
    top: 221px;
    height: 86px;
    padding-left: 10px;
    border-left: 2px solid var(--white);
    white-space: nowrap;
  }
  .contact-phone {
    font-size: 53px;
    line-height: 44px;
    color: var(--white);
  }
  .contact-web {
    font-size: 48px;
    line-height: 44px;
    color: var(--gold-light);
  }
  .scan-tablet {
    position: absolute;
    left: 797px;
    top: 161px;
    width: 98px;
    height: 149px;
    border-radius: 7px;
    background: linear-gradient(90deg, #5a2a20, #b66e57 45%, #8e4b3b 55%, #4a2018);
    border: 7px solid var(--ink);
    border-top-width: 26px;
    border-bottom-width: 26px;
    box-shadow: 0 6px 8px rgba(0,0,0,0.4);
  }
  .portrait {
    position: absolute;
    left: 912px;
    top: 18px;
    width: 198px;
    height: 313px;
    border-radius: 90px 90px 0 0;
    background: linear-gradient(180deg, #d8c3a4 0%, #c9a98a 35%, #38463a 62%, #e9e9e6 80%, #3a4638 100%);
  }
</style>
</head>
<body>
  <section class="billboard">
    <svg class="billboard-bands" viewBox="0 0 1140 331" aria-hidden="true">
      <defs>
        <linearGradient id="goldBand" x1="0" y1="0" x2="1" y2="1">
          <stop offset="0" stop-color="#c79a3a"/>
          <stop offset="1" stop-color="#8e7a3c"/>
        </linearGradient>
      </defs>
      <polygon points="0,0 100,0 0,300" fill="url(#goldBand)"/>
      <polygon points="945,0 1140,0 1140,45 1082,331 880,331" fill="url(#goldBand)"/>
      <polygon points="985,0 1010,0 920,331 895,331" fill="#d7ab46" opacity="0.45"/>
    </svg>

    <div class="brand-plate">
      <span class="brand-dot"></span>
      <span class="brand-name">4D Cradle Glimpse</span>
    </div>

    <ul class="services">
      <li>4D Ultrasound</li>
      <li>Early Gender</li>
      <li>Pregnancy Confirmation</li>
    </ul>

    <h1 class="headline">MEET YOUR BABY<br>BEFORE<span class="script-word">Birth</span></h1>

    <div class="contact">
      <p class="contact-phone">850-471-5923</p>
      <p class="contact-web">4DCRADLEGLIMPSE.COM</p>
    </div>

    <div class="scan-tablet" role="img" aria-label="Tablet showing a 4D ultrasound image of twin babies"></div>

    <div class="portrait" role="img" aria-label="Professional headshot of the studio owner holding an ultrasound probe"></div>
  </section>
</body>
</html>
```